Every Shelf Set Neatly or ESN Organized needs a business card design. ESN Organized is a professi

We need a business card design that is clean, sharp and conveys a sense of organization. I already have a logo.

Target Market(s)

Families (specifically mothers), small business owners, parents, seniors

Industry/Entity Type

Business

Contact Information for Business Card

My website is www.esnorganized-example.com and my Facebook page is http://www.sociallink-example.com/everyshelfsetneatly. The phone number is 418-552-7094 and I want to be listed as Lorna M. Pelham, Owner

Requirements
Must have
• My logo.

```html
<!DOCTYPE html>
<html lang="en">
<head>
<meta charset="utf-8">
<title>Every Shelf Set Neatly — Business Card</title>
<link rel="stylesheet" href="https://fonts.googleapis.com/css2?family=Montserrat:wght@400;500;600&family=Open+Sans:wght@400;600&display=swap">
<style>
  :root {
    --brand-blue: #0b7fdb;
    --brand-blue-soft: #3d98e2;
    --ink: #1c1c1c;
    --paper: #ffffff;
    --backdrop: #eceef1;
  }
  * { margin: 0; padding: 0; box-sizing: border-box; }
  html, body {
    width: 1200px; height: 900px; overflow: hidden;
    background: var(--backdrop);
  }
  .canvas { position: relative; width: 1200px; height: 900px; }

  .card { position: absolute; overflow: hidden; }
  .card--front {
    left: 78px; top: 35px; width: 540px; height: 363px;
    background: var(--brand-blue); color: var(--paper);
  }
  .card--back {
    left: 420px; top: 505px; width: 535px; height: 352px;
    background: var(--paper); color: var(--ink);
  }

  .motif-area { position: absolute; border-radius: 6px; }
  .card--front .motif-area { left: 425px; top: 20px; width: 110px; height: 323px; background: var(--brand-blue-soft); }
  .card--back .motif-area { left: 0; top: 0; width: 150px; height: 352px; background: var(--brand-blue); opacity: .9; }

  .wordmark {
    position: absolute;
    font-family: 'Montserrat', sans-serif; font-weight: 400;
    letter-spacing: 3px; white-space: nowrap;
  }
  .card--front .wordmark { left: 30px; top: 78px; font-size: 25px; color: var(--paper); }
  .card--back .wordmark { left: 200px; top: 185px; font-size: 24px; color: var(--ink); }

  .short-name {
    position: absolute; left: 290px; top: 112px;
    font-family: 'Montserrat', sans-serif; font-weight: 400;
    font-size: 40px; color: var(--brand-blue); letter-spacing: 1px;
    display: flex; align-items: center; gap: 10px;
  }
  .short-name .dot { width: 10px; height: 10px; border-radius: 50%; background: var(--brand-blue); }

  .person { position: absolute; left: 35px; top: 168px; font-family: 'Open Sans', sans-serif; }
  .person__name { font-size: 20px; font-weight: 600; }
  .person__role { font-size: 15px; margin-top: 2px; }

  .contact-list {
    position: absolute; left: 35px; top: 240px; list-style: none;
    font-family: 'Open Sans', sans-serif; font-size: 15.5px; line-height: 24.5px;
  }
  .contact-list li { display: flex; align-items: center; gap: 7px; }
  .contact-list svg { width: 12px; height: 12px; fill: var(--paper); }
</style>
</head>
<body>
<main class="canvas">
  <section class="card card--front" aria-label="Business card front">
    <div class="motif-area" role="img" aria-label="Large decorative clip motif"></div>
    <p class="wordmark">Every Shelf Set Neatly</p>
    <div class="person">
      <p class="person__name">Lorna M. Pelham</p>
      <p class="person__role">Owner</p>
    </div>
    <ul class="contact-list">
      <li><svg viewBox="0 0 24 24" aria-hidden="true"><path d="M6.6 10.8a15 15 0 0 0 6.6 6.6l2.2-2.2a1 1 0 0 1 1-.25 11.4 11.4 0 0 0 3.6.57 1 1 0 0 1 1 1V20a1 1 0 0 1-1 1A17 17 0 0 1 3 4a1 1 0 0 1 1-1h3.5a1 1 0 0 1 1 1c0 1.25.2 2.45.57 3.6a1 1 0 0 1-.25 1z"/></svg>418-552-7094</li>
      <li><svg viewBox="0 0 24 24" aria-hidden="true"><path d="M2 5h20v14H2z M2 5l10 8 10-8" fill="var(--paper)"/><path d="M2 5l10 8 10-8" fill="none" stroke="var(--brand-blue)" stroke-width="2"/></svg>info@esnorganized-example.com</li>
      <li><svg viewBox="0 0 24 24" aria-hidden="true"><circle cx="12" cy="12" r="10"/><path d="M2 12h20M12 2c3 3 3 17 0 20M12 2c-3 3-3 17 0 20" fill="none" stroke="var(--brand-blue)" stroke-width="1.6"/></svg>www.esnorganized-example.com</li>
      <li>everyshelfsetneatly</li>
    </ul>
  </section>

  <section class="card card--back" aria-label="Business card back">
    <div class="motif-area" role="img" aria-label="Large decorative clip motif"></div>
    <p class="short-name"><span class="dot"></span>ESN</p>
    <p class="wordmark">Every Shelf Set Neatly</p>
  </section>
</main>
</body>
</html>
```